business card Calvanto

Wee need a business card design for a new compagny based on Paris
We developped innovative a platform for selling services to refresh, beautify and develop its housing.
We would like a red logo on a black background
Te final design should communicate quality service, know-how, high-end

Target Market(s)

individuals

Industry/Entity Type

Business

```html
<!DOCTYPE html>
<html lang="en">
<head>
<meta charset="utf-8">
<title>Calvanto business card</title>
<link rel="stylesheet" href="https://fonts.googleapis.com/css2?family=Montserrat:wght@700&family=Open+Sans:wght@300;400&display=swap">
<style>
  :root {
    --backdrop: #e4e4e4;
    --card-black: #0d0d0d;
    --card-sheen: #1c1c1c;
    --coral: #e8676a;
    --brand-grey: #9a9a9a;
    --text-grey: #8c8c8c;
  }
  * { box-sizing: border-box; margin: 0; padding: 0; }
  html, body {
    width: 1200px; height: 852px; overflow: hidden;
    background: var(--backdrop);
  }
  .canvas {
    position: relative; width: 1200px; height: 852px;
    display: flex; flex-direction: column; align-items: center; justify-content: center; gap: 40px;
  }
  .card {
    position: relative; width: 600px; height: 343px;
    border-radius: 30px; overflow: hidden;
    background: linear-gradient(125deg, var(--card-black) 0%, var(--card-sheen) 48%, var(--card-black) 70%);
  }
  /* front */
  .card--front { display: flex; align-items: center; justify-content: center; gap: 18px; }
  .brand-square { width: 62px; height: 62px; background: var(--coral); }
  .brand-name {
    font-family: "Open Sans", sans-serif; font-weight: 300;
    font-size: 64px; color: var(--brand-grey); letter-spacing: 1px; line-height: 1;
  }
  /* back */
  .brand-block {
    position: absolute; left: 58px; top: 118px; width: 168px; height: 168px;
    background: var(--coral);
  }
  .card__base { position: absolute; left: 0; right: 0; bottom: 0; height: 12px; background: var(--coral); }
  .contact { position: absolute; left: 300px; top: 64px; font-family: "Open Sans", sans-serif; }
  .contact__name {
    font-family: "Montserrat", sans-serif; font-weight: 700; font-size: 20px; color: var(--coral);
  }
  .contact__role { font-size: 11px; color: var(--text-grey); margin: 2px 0 22px 20px; }
  .contact__list { list-style: none; }
  .contact__item {
    display: flex; align-items: center; gap: 10px;
    font-size: 14px; color: var(--text-grey); line-height: 21px;
  }
  .contact__item svg { width: 12px; height: 12px; flex: none; fill: var(--coral); }
  .contact__address { font-size: 14px; color: var(--text-grey); line-height: 21px; margin-top: 8px; }
</style>
</head>
<body>
<main class="canvas">
  <section class="card card--front" aria-label="Card front">
    <div class="brand-square"></div>
    <span class="brand-name">Calvanto</span>
  </section>

  <section class="card card--back" aria-label="Card back">
    <div class="brand-block"></div>
    <div class="contact">
      <p class="contact__name">Your Long Name</p>
      <p class="contact__role">Managing Director</p>
      <ul class="contact__list">
        <li class="contact__item">
          <svg viewBox="0 0 12 12" aria-hidden="true"><path d="M1 3c0-1 1-2 2-2h6c1 0 2 1 2 2v1H8V3H4v1H1zM2 5h8l1 6H1z"/></svg>
          00.00.00.0000
        </li>
        <li class="contact__item">
          <svg viewBox="0 0 12 12" aria-hidden="true"><rect x="3" y="0" width="6" height="12" rx="1"/></svg>
          00.00.00.0000
        </li>
        <li class="contact__item">
          <svg viewBox="0 0 12 12" aria-hidden="true"><path d="M0 2h12v8H0zM0 2l6 5 6-5"/></svg>
          yourname@yourwebsite.com
        </li>
        <li class="contact__item">
          <svg viewBox="0 0 12 12" aria-hidden="true"><circle cx="6" cy="6" r="6"/></svg>
          www.yourwebsite.com
        </li>
      </ul>
      <p class="contact__address">Your Commercial or office address<br>in just two line with pincode</p>
    </div>
    <div class="card__base"></div>
  </section>
</main>
</body>
</html>
```